Professional, Attractive, Simple Website Needed!!

We completed the design for our logo.

We need a website built out around this.

Here are a couple samples of how we want ours formatted.

http://brimvoltco.com

http://www.ravelbeam.com/lp/free-quote?LeadSource=Search%20Engine&ProgramName=searchads&experience=qual&language=en&type=brd&gclid=Xk7PLmqwTRZBNVuEYcaHdFgWsLoPeRtQnMxVbCzJaKiOuYtReWqAsDfGhJkLzXcVbNmQwErTyUiOpAsDfGhJkLzX_wcB

http://quorel.co
Updates

Project Deadline Extended
Reason: Extending this deadline due to our delay in providing designers with content for each page. This is coming in next 24 hours.

Project Deadline Extended
Reason: Due to scheduling conflicts and extended travel delays related to Puerto Rico, the deadline has been extended. Your patience is greatly appreciated.

Project Deadline Extended
Reason: Travel and scheduling conflicts have made it impossible to give this project the thorough review it deserves, therefore I am extending the deadline. Thank you for your patience!

Target Market(s)

Home Owners who earn 60k + household annually

Industry/Entity Type

It Professional

Coding

Coded - Design and coding required

Number of Pages Required

5+ page

Font styles to use
Serif

Colors
34a7d8
9bcb3c

Requirements
Must have
• Simple
• Lead form Entry (Ability for visitor to enter Name, number and address for a quote)
• Sleek Design
• Professional
• Testimonials
• Use color Scheme of Design Logo Attached
Nice to have
• Video when site starts
• Like this
• https://www.vidplexa.com/watch?v=Qm8rTbLw3Np&feature=vidplexa.be
Should not have
• Should not include Commercial solar
• Should not include wind power

```html
<!DOCTYPE html>
<html lang="en">
<head>
<meta charset="utf-8">
<title>Brightfield Energy – Solar Savings</title>
<link href="https://fonts.googleapis.com/css2?family=Quicksand:wght@400;500;600&family=Lato:wght@400;700&display=swap" rel="stylesheet">
<style>
:root{
  --blue:#34a7d8;
  --blue-deep:#1f8fc6;
  --green:#9bcb3c;
  --green-deep:#7fb22a;
  --ink:#555;
  --ink-soft:#777;
  --grey-band:#efefef;
  --white:#fff;
  --line:#d9d9d9;
}
*{box-sizing:border-box;margin:0;padding:0}
html,body{width:1200px;height:3125px;overflow:hidden;background:var(--white)}
body{font-family:'Lato',sans-serif;color:var(--ink);position:relative}
.accent{color:var(--green)}
section,header,footer,nav{position:absolute;left:0;width:1200px}

/* header */
.site-header{top:0;height:115px;display:flex;align-items:center;justify-content:center;gap:10px}
.brand-dot{width:40px;height:40px;border-radius:50%;background:var(--blue)}
.brand-name{font-family:'Quicksand',sans-serif;font-weight:600;font-size:26px;color:var(--blue)}
.main-nav{top:115px;height:52px;background:var(--blue);display:flex;justify-content:center;align-items:center;gap:34px}
.main-nav a{color:var(--white);text-decoration:none;font-family:'Quicksand',sans-serif;font-size:17px;font-weight:500}
.main-nav a.active{color:var(--green)}

/* hero */
.hero{top:167px;height:573px;background:linear-gradient(115deg,#e9f3fb 0%,#a9c7e6 30%,#3f6fb4 60%,#1f3c7c 100%)}
.hero-photo{position:absolute;right:0;top:0;width:700px;height:573px;background:linear-gradient(100deg,rgba(40,30,45,0) 0%,rgba(40,30,45,.45) 30%,rgba(20,30,60,.6) 100%)}
.hero-title{position:absolute;left:77px;top:176px;font-family:'Quicksand',sans-serif;font-weight:500;font-size:42px;line-height:52px;color:var(--blue);text-transform:uppercase}
.btn-pill{position:absolute;left:79px;top:341px;width:188px;height:46px;border-radius:23px;background:var(--green);color:var(--white);font-family:'Quicksand',sans-serif;font-size:19px;font-weight:600;display:flex;align-items:center;justify-content:center;text-transform:uppercase;box-shadow:0 2px 0 var(--green-deep)}

/* benefits */
.benefits{top:740px;height:280px}
.benefit{position:absolute;top:47px;width:240px;text-align:center}
.benefit-circle{width:146px;height:146px;border-radius:50%;margin:0 auto;display:flex;align-items:center;justify-content:center}
.benefit-circle.blue{background:radial-gradient(circle,#d8eef9 40%,#a8d8ef 100%);border:3px solid var(--blue)}
.benefit-circle.green{background:radial-gradient(circle,#eef6dc 40%,#cfe6a2 100%);border:3px solid var(--green)}
.benefit-label{margin-top:22px;font-family:'Quicksand',sans-serif;font-size:22px;color:#666}

/* why */
.why{top:1020px;height:448px;background:var(--grey-band)}
.why-video{position:absolute;left:79px;top:63px;width:500px;height:312px;background:linear-gradient(160deg,#6f8d5a 0%,#a9b79a 45%,#c9b9a5 70%,#5b6c85 100%);box-shadow:0 3px 8px rgba(0,0,0,.3)}
.play-btn{position:absolute;left:222px;top:128px;width:56px;height:40px;border-radius:10px;background:var(--white);display:flex;align-items:center;justify-content:center}
.why-card{position:absolute;left:587px;top:78px;width:538px;min-height:277px;background:var(--white);padding:28px 22px 22px 30px;text-align:right}
.section-title{font-family:'Quicksand',sans-serif;font-weight:500;font-size:44px;color:var(--blue)}
.why-card .section-title{text-align:left;font-size:40px;line-height:48px;white-space:nowrap}
.why-card p{margin-top:12px;font-size:15px;line-height:25px;color:var(--ink)}

/* how */
.how{top:1468px;height:428px}
.how .section-title{position:absolute;top:40px;width:100%;text-align:center}
.step{position:absolute;top:125px;width:250px;text-align:center}
.step-circle{width:156px;height:156px;border-radius:50%;margin:0 auto;background:var(--white);box-shadow:0 4px 6px rgba(0,0,0,.15);border-bottom:3px solid var(--green);display:flex;align-items:center;justify-content:center}
.step-name{margin-top:22px;font-family:'Quicksand',sans-serif;font-size:23px;color:var(--blue);font-weight:500}
.step-desc{margin:4px auto 0;width:220px;font-size:14px;line-height:20px;color:var(--ink-soft)}
.step-arrow{position:absolute;top:185px;color:var(--green);font-size:34px;font-family:'Quicksand',sans-serif}

/* testimonials + blog */
.stories{top:1896px;height:489px;background:var(--grey-band)}
.stories .section-title{position:absolute;top:42px}
.avatar{position:absolute;left:87px;top:146px;width:88px;height:88px;border-radius:50%;background:linear-gradient(#c9a78d,#8b5e44);border:3px solid var(--white)}
.quote-box{position:absolute;left:198px;top:150px;width:333px;height:152px;background:#f5f5f5;box-shadow:0 1px 4px rgba(0,0,0,.25);padding:16px 22px}
.quote-box h3{font-family:'Quicksand',sans-serif;font-weight:500;font-size:21px;line-height:26px;color:var(--green)}
.quote-box p{margin-top:4px;font-size:14px;line-height:22px;color:var(--ink)}
.quote-author{position:absolute;left:200px;top:327px;font-size:14px;font-weight:700;color:var(--ink)}
.slider-btn{position:absolute;top:356px;width:30px;height:30px;background:#d6d6d6;color:#555;font-size:18px;display:flex;align-items:center;justify-content:center}
.post{position:absolute;left:629px;width:494px;height:90px;border-bottom:1px solid var(--line)}
.post-date{position:absolute;left:0;top:0;width:62px;height:62px;background:var(--blue-deep);color:var(--white);text-align:center;padding-top:8px}
.post-date b{display:block;font-size:22px;line-height:24px}
.post-date span{font-size:13px}
.post-body{position:absolute;left:79px;top:0}
.post-body h4{font-family:'Quicksand',sans-serif;font-weight:500;font-size:16px;color:var(--green)}
.post-body p{font-size:14px;line-height:24px;color:var(--ink)}
.view-more{position:absolute;left:635px;top:430px;font-family:'Quicksand',sans-serif;font-size:16px;color:var(--blue-deep)}

/* lead form */
.lead{top:2385px;height:521px}
.lead .section-title{position:absolute;top:40px;width:100%;text-align:center}
.lead-form{position:absolute;left:287px;top:112px;width:625px;height:358px;background:#eaf5fa;border:3px solid var(--blue)}
.field{position:absolute;left:53px;width:490px;border-bottom:1px solid var(--blue);font-size:15px;font-style:italic;color:#666;padding-bottom:4px}
.btn-send{position:absolute;left:468px;top:282px;width:104px;height:48px;border:2px solid var(--blue);border-radius:24px;color:var(--blue);font-family:'Quicksand',sans-serif;font-size:19px;display:flex;align-items:center;justify-content:center}

/* footer */
.site-footer{top:2906px;height:219px;background:var(--blue)}
.footer-nav{position:absolute;left:77px;top:22px;display:flex;align-items:center;gap:36px}
.footer-nav a{color:var(--white);text-decoration:none;font-size:15px}
.footer-nav a.active{border:2px solid var(--green);border-radius:20px;padding:8px 18px;color:var(--green)}
.social{position:absolute;right:77px;top:32px;display:flex;gap:26px}
.social span{width:20px;height:20px;border-radius:50%;background:var(--white)}
.social span:first-child{background:var(--green)}
.footer-rule{position:absolute;left:77px;right:77px;top:80px;border-top:1px solid var(--green)}
.footer-title{position:absolute;left:143px;top:88px;font-family:'Quicksand',sans-serif;font-size:21px;color:var(--green)}
.contact-item{position:absolute;top:142px;display:flex;align-items:center;gap:14px;color:var(--white);font-size:15px;line-height:20px}
.contact-icon{width:50px;height:50px;border-radius:50%;display:flex;align-items:center;justify-content:center}
.contact-icon.green{background:var(--green)}
.contact-icon.white{background:var(--white)}
.copyright{position:absolute;right:77px;top:158px;color:var(--white);font-size:15px}
.copyright em{font-style:normal;color:var(--green)}
</style>
</head>
<body>

<header class="site-header">
  <span class="brand-dot"></span>
  <span class="brand-name">Brightfield Energy</span>
</header>

<nav class="main-nav">
  <a class="active" href="#">Home</a>
  <a href="#">Why Brightfield Energy</a>
  <a href="#">How It Works</a>
  <a href="#">Testimonials</a>
  <a href="#">Blog</a>
  <a href="#">Contact</a>
</nav>

<section class="hero">
  <div class="hero-photo" role="img" aria-label="Installer lifting a solar panel against a bright blue sky"></div>
  <h1 class="hero-title">Solar Savings<br>with Brightfield<br>Energy</h1>
  <a class="btn-pill">Contact Us</a>
</section>

<section class="benefits">
  <div class="benefit" style="left:217px">
    <div class="benefit-circle blue">
      <svg width="70" height="70" viewBox="0 0 70 70" fill="none" stroke="#1f6fa8" stroke-width="4"><circle cx="35" cy="35" r="27"/><path d="M42 25c-3-3-14-3-14 3s14 4 14 10-11 6-14 2M35 18v34"/><path d="M15 15l40 40"/></svg>
    </div>
    <div class="benefit-label">Zero Cost</div>
  </div>
  <div class="benefit" style="left:480px">
    <div class="benefit-circle green">
      <svg width="70" height="70" viewBox="0 0 70 70" fill="none" stroke="#6a9a20" stroke-width="4"><path d="M15 12h40v28L35 60 15 40z"/><path d="M38 18l-10 16h10l-6 14 12-18H34z"/></svg>
    </div>
    <div class="benefit-label">Lower Energy Bills</div>
  </div>
  <div class="benefit" style="left:728px">
    <div class="benefit-circle blue">
      <svg width="70" height="70" viewBox="0 0 70 70" fill="none" stroke="#1a4f86" stroke-width="5"><circle cx="35" cy="35" r="27"/><path d="M22 48l20-20M44 22a6 6 0 1 0 4 4M22 22l26 26"/></svg>
    </div>
    <div class="benefit-label">No Maintenance</div>
  </div>
</section>

<section class="why">
  <div class="why-video" role="img" aria-label="Video still of an installer fitting solar panels on a rooftop">
    <span class="play-btn"><svg width="22" height="22" viewBox="0 0 22 22"><path d="M5 3l14 8-14 8z" fill="#e02020"/></svg></span>
  </div>
  <div class="why-card">
    <h2 class="section-title">Why <span class="accent">Brightfield Energy</span></h2>
    <p>Lorem Ipsum is simply dummy text of the printing and typesetting industry. Lorem Ipsum has been the industry's standard dummy text ever since the 1500s, when an unknown printer took a galley of type and scrambled it to make a type specimen book. It has survived not only five centuries, but also the leap into electronic typesetting, remaining essentially unchanged.</p>
  </div>
</section>

<section class="how">
  <h2 class="section-title">How <span class="accent">It Works</span></h2>
  <div class="step" style="left:73px">
    <div class="step-circle"><svg width="80" height="80" viewBox="0 0 80 80"><circle cx="30" cy="38" r="10" fill="#1f8fc6"/><path d="M12 68c0-12 8-18 18-18s18 6 18 18z" fill="#1f8fc6"/><rect x="36" y="10" width="32" height="22" rx="3" fill="none" stroke="#1f8fc6" stroke-width="3"/><path d="M42 18h20M42 24h14" stroke="#1f8fc6" stroke-width="2"/></svg></div>
    <div class="step-name">Speak Consultant</div>
    <div class="step-desc">Speak to a solar consultant</div>
  </div>
  <div class="step-arrow" style="left:320px">»</div>
  <div class="step" style="left:342px">
    <div class="step-circle"><svg width="80" height="80" viewBox="0 0 80 80"><circle cx="56" cy="20" r="8" fill="none" stroke="#f0a020" stroke-width="3"/><path d="M12 36h44l6 24H6z" fill="none" stroke="#1f8fc6" stroke-width="3"/><path d="M34 36v24M9 48h50" stroke="#1f8fc6" stroke-width="2"/><path d="M28 60v8h12v-8" stroke="#1f8fc6" stroke-width="3" fill="none"/></svg></div>
    <div class="step-name">Design</div>
    <div class="step-desc">We will design your solar panel system</div>
  </div>
  <div class="step-arrow" style="left:588px">»</div>
  <div class="step" style="left:608px">
    <div class="step-circle"><svg width="80" height="80" viewBox="0 0 80 80" fill="none" stroke="#1f8fc6" stroke-width="3"><rect x="12" y="16" width="56" height="50" rx="3"/><path d="M12 28h56M26 10v10M54 10v10"/><path d="M22 38h8M36 38h8M50 38h8M22 50h8M36 50h8M50 50h8" stroke-width="5"/></svg></div>
    <div class="step-name">Schedule</div>
    <div class="step-desc">Schedule your 1 day install</div>
  </div>
  <div class="step-arrow" style="left:855px">»</div>
  <div class="step" style="left:875px">
    <div class="step-circle"><svg width="80" height="80" viewBox="0 0 80 80"><circle cx="44" cy="24" r="12" fill="#1f8fc6"/><path d="M10 54h14l14 6 26-12c4-2 6 3 2 5L40 68 22 64H10z" fill="#1f8fc6"/></svg></div>
    <div class="step-name">Start Savings</div>
    <div class="step-desc">Start saving on you electricity bill</div>
  </div>
</section>

<section class="stories">
  <h2 class="section-title" style="left:77px">Tetimonials</h2>
  <div class="avatar" role="img" aria-label="Customer portrait"></div>
  <div class="quote-box">
    <h3>Sunhaven just saved<br>my life!</h3>
    <p>Lorem Ipsum is simply dummy text of the printing and typesetting industry. Lorem Ipsum.</p>
  </div>
  <div class="quote-author">- Marla Quinn</div>
  <span class="slider-btn" style="left:79px">‹</span>
  <span class="slider-btn" style="left:546px">›</span>

  <h2 class="section-title" style="left:629px">Latest <span class="accent">Blog</span></h2>
  <div class="post" style="top:118px">
    <div class="post-date"><b>21</b><span>mar</span></div>
    <div class="post-body"><h4>The Dream Act of 2017</h4><p>On July 20 two United State Senators, one Republican and<br>one Democrat, introduced the Dream Act of 2017.</p></div>
  </div>
  <div class="post" style="top:224px">
    <div class="post-date"><b>21</b><span>mar</span></div>
    <div class="post-body"><h4>Narrowed Travel Ban Takes Effect</h4><p>On July 20 two United State Senators, one Republican and<br>one Democrat, introduced the Dream Act of 2017.</p></div>
  </div>
  <div class="post" style="top:328px;border-bottom:none">
    <div class="post-date"><b>21</b><span>mar</span></div>
    <div class="post-body"><h4>USCIS Increases The H2-B Cap By 15,000</h4><p>On July 20 two United State Senators, one Republican and<br>one Democrat, introduced the Dream Act of 2017.</p></div>
  </div>
  <a class="view-more">View More ›</a>
</section>

<section class="lead">
  <h2 class="section-title">Solar <span class="accent">Works for you</span></h2>
  <form class="lead-form">
    <div class="field" style="top:52px">Name</div>
    <div class="field" style="top:124px">Email</div>
    <div class="field" style="top:238px">Message</div>
    <span class="btn-send">SEND</span>
  </form>
</section>

<footer class="site-footer">
  <nav class="footer-nav">
    <a class="active" href="#">Home</a>
    <a href="#">Why Brightfield Energy</a>
    <a href="#">How It Works</a>
    <a href="#">Testimonials</a>
    <a href="#">Blog</a>
    <a href="#">Contact</a>
  </nav>
  <div class="social" aria-label="Social links"><span></span><span></span><span></span></div>
  <div class="footer-rule"></div>
  <div class="footer-title">Contact Us</div>
  <div class="contact-item" style="left:79px">
    <span class="contact-icon green"><svg width="24" height="24" viewBox="0 0 24 24"><path d="M12 3L2 12h3v9h5v-6h4v6h5v-9h3z" fill="#fff"/></svg></span>
    <span>123, building, street, city,<br>country, zipcode.</span>
  </div>
  <div class="contact-item" style="left:360px">
    <span class="contact-icon white"><svg width="24" height="24" viewBox="0 0 24 24"><path d="M6 2l4 4-2 3c1 3 4 6 7 7l3-2 4 4-3 4C10 22 2 14 2 5z" fill="#9bcb3c"/></svg></span>
    <span>123 456 7890</span>
  </div>
  <div class="contact-item" style="left:545px">
    <span class="contact-icon white"><svg width="24" height="24" viewBox="0 0 24 24"><rect x="6" y="2" width="12" height="20" rx="2" fill="#9bcb3c"/><rect x="8" y="5" width="8" height="12" fill="#fff"/></svg></span>
    <span>123 456 9999</span>
  </div>
  <div class="copyright">©<em>Brightfield Energy</em> 2017 - All Rights Reserved.</div>
</footer>

</body>
</html>
```